Valdane Companies Business Card Design

We need a new business card for our Private Equity Real Estate Development firm, “Valdane” and our EB-5 regional center “Thornmere Regional Center” on one card. We prefer a design that is simple, elegant, and represents the luxury products we design and build as well as the financial security and stability our successful history has produced. We are an industry leader in our field and 3rd generation family business that has evolved into an institutional quality investment platform. Considered design size is standard business card dimensions (3.5 x 2 inches with an additional 1/8 inch space for design elements or backgrounds that extend beyond the finished size of your piece.

Target Market(s)

• High net worth individuals
• Highly skilled technical workers and physicians in the US seeking investment-based immigration opportunities
• Sophisticated private equity investors
• Intermediary partners include domestic attorneys and investment brokers, as well as international agent networks
• US real estate developers

Industry/Entity Type

Finance

Contact Information for Business Card

(Providing placeholder info for personal information, please design for longer character spaces, longer names and addresses etc..)
• Logo for Valdane
• Logo for Thornmere Regional Center
• Full name: Marcus Valdane
• Job title: CEO
• Email address: mvaldane@valdanecompanies.com
• Cell phone number: +1.555.314.2287
• Office number +1.555.628.4410
• Office address: Larkfield Court 5, 4817 Vista Orilla, San Ramon, CA.
• Website: www.valdanecompanies.com

Font styles to use
Serif
Sans Serif

Colors
ec1f27
ffffff
000000

Requirements
Must have
• • Logo for Valdane
• • Logo for Thornmere Regional Center
• - Use rounded corners
• (See .ai file included for logos)
Nice to have
• • Simple, elegant design
• • Aesthetically compatible with our website design (www.valdanecompanies.com)
• • Color palette including but not limited to white, black, and red (as per logos)
Should not have
• - Not too much red color
• - Do not stack both logos on top of each other

```html
<!DOCTYPE html>
<html lang="en">
<head>
<meta charset="utf-8">
<title>Valdane Companies Business Card</title>
<link rel="stylesheet" href="https://fonts.googleapis.com/css2?family=Crimson+Pro:wght@500;600;700&family=Roboto:wght@400;500&display=swap">
<style>
  :root {
    --stage: #2b2b2b;
    --paper: #f2f2f2;
    --crimson: #a0154a;
    --crimson-dark: #7d0f38;
    --crimson-light: #b81d57;
    --ink: #1a1a1a;
    --text-grey: #444;
    --steel: #a9a9a9;
    --white: #ffffff;
  }
  * { margin: 0; padding: 0; box-sizing: border-box; }
  html, body { width: 1200px; height: 960px; overflow: hidden; }
  body { background: var(--stage); position: relative; font-family: "Roboto", Arial, sans-serif; }

  .card { position: absolute; width: 600px; height: 343px; box-shadow: 0 3px 8px rgba(0,0,0,.5); overflow: hidden; }

  /* Front */
  .card-front { left: 314px; top: 113px; background: var(--paper); }
  .center-name {
    position: absolute; left: 36px; top: 66px;
    display: flex; align-items: center; gap: 10px;
    font-family: "Crimson Pro", Georgia, serif; font-weight: 700;
    font-size: 15px; letter-spacing: .3px; color: var(--crimson);
    text-transform: uppercase; white-space: nowrap; line-height: 1;
  }
  .center-name .mark { width: 26px; height: 26px; background: var(--crimson); flex: none; }
  .holder { position: absolute; right: 40px; top: 61px; text-align: right; font-family: "Crimson Pro", Georgia, serif; white-space: nowrap; }
  .holder-name { font-weight: 700; font-size: 20px; color: var(--crimson); text-transform: uppercase; line-height: 1; }
  .holder-title { font-weight: 500; font-size: 16px; color: var(--ink); margin-top: 4px; line-height: 1; }

  .contact-band {
    position: absolute; left: 0; top: 161px; width: 600px; height: 138px;
    background: radial-gradient(ellipse at 45% 40%, var(--crimson-light), var(--crimson) 55%, var(--crimson-dark));
    color: var(--white); font-size: 14px; line-height: 18px;
  }
  .contact-band .steel { position: absolute; right: 0; top: 0; width: 110px; height: 100%; background: var(--steel); }
  .address { position: absolute; left: 35px; top: 20px; }
  .lines { position: absolute; left: 35px; top: 82px; white-space: nowrap; }
  .lines b { font-weight: 500; }
  .website { position: absolute; left: 35px; top: 309px; font-size: 14px; color: var(--text-grey); }

  /* Back */
  .card-back {
    left: 311px; top: 472px;
    background: radial-gradient(ellipse at 50% 38%, var(--crimson-light), var(--crimson) 55%, var(--crimson-dark));
  }
  .brand {
    position: absolute; left: 0; top: 190px; width: 100%; text-align: center;
    font-family: "Crimson Pro", Georgia, serif; font-weight: 700; font-size: 40px;
    letter-spacing: 2px; color: var(--white); text-transform: uppercase; white-space: nowrap;
  }
  .brand-dot { position: absolute; left: 270px; top: 95px; width: 60px; height: 60px; border-radius: 50%; background: var(--crimson-dark); }
</style>
</head>
<body>
  <section class="card card-front">
    <div class="center-name"><span class="mark"></span>Thornmere Regional Center</div>
    <div class="holder">
      <div class="holder-name">Marcus Valdane</div>
      <div class="holder-title">CEO</div>
    </div>
    <div class="contact-band">
      <div class="steel"></div>
      <div class="address">Larkfield Court 5<br>4817 Vista Orilla<br>San Ramon, CA.</div>
      <div class="lines">
        <b>Phone:</b> +1.555.628.4410&nbsp; <b>Cell:</b> +1.555.314.2287<br>
        mvaldane@valdanecompanies.com
      </div>
    </div>
    <div class="website">www.valdanecompanies.com</div>
  </section>

  <section class="card card-back">
    <span class="brand-dot"></span>
    <div class="brand">Valdane Capital</div>
  </section>
</body>
</html>
```